Redesign of the UI of a customer service platform

To improve the user experience of our customers, we need a new design for our agent interface of our customer service platform (quindelo.com).
The focus will be on the dashboard and the inbox screens (see attached) along with the common UI elements (Buttons, menu, fonts, forms...)
We want a simple and distinctive design

Target Market(s)

Worldwide

Industry/Entity Type

It Service

Number of Pages Required

3 page

Font styles to use
Sans Serif

Requirements
Must have
• New Onboarding page: this is a new page that is shown to user the first time they login to the platform. This will replace the current onboarding screen (setup SMS, Setup widget...etc)
• Dashboard page: to access important information and activate services (see screenshot from current site)
• Inbox page: to manage all the interactions with customers. (see screenshot from current site)
• UI elements (buttons, menus, forms, tables, fonts, color palette)

```html
<!DOCTYPE html>
<html lang="en">
<head>
<meta charset="utf-8">
<title>quindelo — Dashboard</title>
<link href="https://fonts.googleapis.com/css2?family=Montserrat:wght@400;500;600;700&display=swap" rel="stylesheet">
<style>
:root{
  --blue:#0a93f0;
  --royal:#0062ff;
  --green:#00a800;
  --orange:#ffa200;
  --sky:#57b7e4;
  --ink:#111;
  --muted:#9a9a9a;
  --line:#ececec;
  --white:#fff;
}
*{box-sizing:border-box;margin:0;padding:0}
html,body{width:1073px;height:1200px;overflow:hidden;background:var(--white)}
body{font-family:"Montserrat",sans-serif;color:var(--ink);position:relative}
.abs{position:absolute}
.topbar{left:0;top:0;width:1073px;height:57px;border-bottom:1px solid var(--line)}
.brand{left:20px;top:14px;font-size:21px;font-weight:700;color:#333;display:flex;align-items:center;gap:6px}
.brand .dot{width:14px;height:14px;border-radius:50%;background:#333}
.avatar{left:748px;top:7px;width:41px;height:41px;border-radius:50%;background:radial-gradient(circle at 50% 45%,#c99a74,#5d7f9a);border:3px solid var(--blue)}
.user{left:797px;top:13px;font-size:12px;line-height:15px}
.user b{font-weight:700}
.user span{display:block;color:var(--muted);font-size:11.5px}
.tb-sep{top:0;width:1px;height:57px;background:var(--line)}
.tb-icon{top:17px;width:22px;height:22px}
.menu-btn{left:1030px;top:16px;width:28px;height:26px;border-radius:3px;background:var(--blue)}
.sidebar{left:0;top:57px;width:103px;height:1143px;border-right:1px solid var(--line)}
.nav-item{left:0;width:103px;text-align:center;font-size:11.5px;color:#222}
.nav-item svg{display:block;margin:0 auto 8px}
.page-title{left:122px;top:78px;font-size:13.5px;font-weight:500;display:flex;align-items:center;gap:10px}
.date{right:15px;top:79px;font-size:13.5px}
.stats{left:122px;top:113px;width:937px;height:114px;border:1px solid var(--line);border-left:0}
.stat-tile{top:113px;width:79px;height:114px;color:var(--white);font-size:11.5px;font-weight:500;text-align:center;line-height:17px;padding-top:25px}
.stat-tile .ico{height:30px;display:flex;align-items:center;justify-content:center;margin-bottom:6px}
.stat-val{top:143px;font-size:30px;font-weight:400;color:#333}
.stat-sub{top:179px;font-size:11px;color:var(--muted)}
.reports-h{left:0;width:1073px;padding-left:110px;text-align:center;top:274px;font-size:16px;font-weight:600}
.panel{left:124px;top:319px;width:935px;height:579px;border:1px solid var(--line)}
.panel-rule{left:124px;top:424px;width:935px;height:1px;background:var(--line)}
.report-title{left:183px;top:353px;font-size:13px;font-weight:600;color:var(--blue)}
.report-sub{left:185px;top:376px;font-size:10px}
.btn-green{left:728px;top:354px;width:37px;height:35px;border-radius:2px;background:var(--green)}
.btn-orange{left:988px;top:354px;width:55px;height:35px;border-radius:2px;background:var(--orange)}
.chart{left:124px;top:440px}
.promo{top:934px;width:454px;height:175px;color:var(--white);padding:24px 18px}
.promo h2{font-size:22px;font-weight:700;display:flex;align-items:center;gap:14px;margin-bottom:16px}
.promo p{font-size:13px;line-height:22px;margin-bottom:12px}
.promo .cta{display:inline-block;background:var(--white);color:#333;font-size:11px;font-weight:700;padding:8px 23px;border-radius:2px}
.plans{left:124px;background:var(--green)}
.addons{left:605px;background:var(--orange)}
.footer-rule{left:103px;top:1154px;width:970px;height:1px;background:var(--line)}
.footer{left:103px;width:930px;top:1170px;text-align:center;font-size:11.5px}
.version{right:15px;top:1170px;font-size:11.5px}
</style>
</head>
<body>

<header class="abs topbar"></header>
<div class="abs brand"><span class="dot"></span>quindelo</div>
<div class="abs avatar" role="img" aria-label="Agent profile photo"></div>
<div class="abs user"><b>Owen Marsh</b><span>Available</span></div>
<div class="abs tb-sep" style="left:891px"></div>
<div class="abs tb-sep" style="left:933px"></div>
<div class="abs tb-sep" style="left:976px"></div>
<div class="abs tb-sep" style="left:1018px"></div>
<svg class="abs tb-icon" style="left:902px" viewBox="0 0 22 22"><path d="M3 11 L6 4 H16 L19 11 V18 H3Z" fill="var(--blue)"/><path d="M5 11 H8 L9 13 H13 L14 11 H17" stroke="#fff" stroke-width="1.6" fill="none"/></svg>
<svg class="abs tb-icon" style="left:944px" viewBox="0 0 22 22"><g transform="rotate(-45 11 11)"><rect x="2" y="7" width="18" height="8" rx="1" fill="var(--blue)"/><line x1="8" y1="8" x2="8" y2="14" stroke="#fff" stroke-width="1.4" stroke-dasharray="1.5 1.2"/></g></svg>
<svg class="abs tb-icon" style="left:986px" viewBox="0 0 22 22"><circle cx="11" cy="11" r="10" fill="var(--blue)"/><text x="11" y="16" text-anchor="middle" font-family="Montserrat,sans-serif" font-weight="700" font-size="13" fill="#fff">?</text></svg>
<div class="abs menu-btn"></div>
<svg class="abs" style="left:1037px;top:22px" width="14" height="14" viewBox="0 0 14 14"><path d="M2 3H12M2 7H12M2 11H12" stroke="#fff" stroke-width="2"/></svg>

<nav class="abs sidebar"></nav>
<div class="abs nav-item" style="top:106px"><svg width="24" height="20" viewBox="0 0 24 20"><path d="M2 17 A10 10 0 1 1 22 17Z" fill="var(--blue)"/><path d="M12 16 L15 8" stroke="#fff" stroke-width="2"/><circle cx="6" cy="12" r="1.4" fill="#fff"/><circle cx="8" cy="7" r="1.4" fill="#fff"/><circle cx="18" cy="12" r="1.4" fill="#fff"/></svg>DASHBOARD</div>
<div class="abs nav-item" style="top:180px"><svg width="22" height="18" viewBox="0 0 22 18"><path d="M2 9 L5 2 H17 L20 9 V16 H2Z" fill="var(--blue)"/><path d="M4 9 H8 L9 11 H13 L14 9 H18" stroke="#fff" stroke-width="1.6" fill="none"/></svg>INBOX</div>
<div class="abs nav-item" style="top:244px"><svg width="24" height="24" viewBox="0 0 24 24"><g transform="rotate(-45 12 12)"><rect x="2" y="8" width="20" height="8" rx="1" fill="var(--blue)"/><line x1="8" y1="9" x2="8" y2="15" stroke="#fff" stroke-width="1.4" stroke-dasharray="1.5 1.2"/></g></svg>TICKETS</div>
<div class="abs nav-item" style="top:316px"><svg width="24" height="22" viewBox="0 0 24 22"><rect x="8" y="1" width="8" height="5" rx="1" fill="none" stroke="var(--blue)" stroke-width="2"/><rect x="1" y="5" width="22" height="16" rx="2" fill="var(--blue)"/><line x1="1" y1="12" x2="23" y2="12" stroke="#fff" stroke-width="1.5"/></svg>CLIENTS</div>
<div class="abs nav-item" style="top:385px"><svg width="20" height="24" viewBox="0 0 20 24"><path d="M2 1 H13 L18 6 V23 H2Z" fill="none" stroke="var(--blue)" stroke-width="2"/><path d="M6 11H14M6 15H14M6 19H14" stroke="var(--blue)" stroke-width="1.6"/></svg>REPORTS</div>
<div class="abs nav-item" style="top:452px"><svg width="26" height="24" viewBox="0 0 26 24"><circle cx="9" cy="14" r="6" fill="var(--blue)"/><circle cx="9" cy="14" r="2.2" fill="#fff"/><circle cx="19" cy="6" r="4.5" fill="var(--blue)"/><circle cx="19" cy="6" r="1.6" fill="#fff"/><circle cx="20" cy="19" r="3.5" fill="var(--blue)"/></svg>SETTINGS</div>
<div class="abs nav-item" style="top:1098px;line-height:16px"><svg width="22" height="18" viewBox="0 0 22 18"><rect x="1" y="2" width="20" height="14" rx="1.5" fill="none" stroke="var(--blue)" stroke-width="2"/><path d="M2 3 L11 10 L20 3" fill="none" stroke="var(--blue)" stroke-width="2"/></svg>SEND<br>FEEDBACK</div>

<div class="abs page-title"><svg width="24" height="20" viewBox="0 0 24 20"><path d="M2 17 A10 10 0 1 1 22 17Z" fill="var(--blue)"/><path d="M12 16 L15 8" stroke="#fff" stroke-width="2"/><circle cx="6" cy="12" r="1.4" fill="#fff"/><circle cx="18" cy="12" r="1.4" fill="#fff"/></svg>DASHBOARD</div>
<div class="abs date">December 9th | 2017</div>

<section class="abs stats"></section>
<div class="abs stat-tile" style="left:122px;background:var(--green)"><div class="ico"><svg width="22" height="24" viewBox="0 0 22 24"><circle cx="11" cy="7" r="6" fill="#fff"/><path d="M1 23 Q1 14 11 14 Q21 14 21 23Z" fill="#fff"/></svg></div>TOTAL<br>CLIENTS</div>
<div class="abs stat-val" style="left:218px">0/0</div>
<div class="abs stat-sub" style="left:218px">Served / Non Served</div>
<div class="abs stat-tile" style="left:343px;background:var(--royal)"><div class="ico"><svg width="26" height="26" viewBox="0 0 24 24"><g transform="rotate(-45 12 12)"><rect x="2" y="8" width="20" height="8" rx="1" fill="none" stroke="#fff" stroke-width="2"/><line x1="8" y1="9" x2="8" y2="15" stroke="#fff" stroke-width="1.4" stroke-dasharray="1.5 1.2"/></g></svg></div>CLIENT<br>TICKETS</div>
<div class="abs stat-val" style="left:440px">0/0</div>
<div class="abs stat-sub" style="left:441px">Open / Closed</div>
<div class="abs stat-tile" style="left:578px;background:var(--orange)"><div class="ico"><svg width="28" height="24" viewBox="0 0 28 24"><ellipse cx="12" cy="9" rx="10" ry="7" fill="none" stroke="#fff" stroke-width="2"/><path d="M16 18 Q22 19 25 15" fill="none" stroke="#fff" stroke-width="2"/></svg></div>TOTAL CHAT<br>MESSAGES</div>
<div class="abs stat-val" style="left:674px">0/0</div>
<div class="abs stat-tile" style="left:801px;background:var(--sky)"><div class="ico"><svg width="16" height="26" viewBox="0 0 16 26"><rect x="1" y="1" width="14" height="24" rx="2" fill="#fff"/><rect x="3" y="4" width="10" height="15" fill="var(--sky)"/><circle cx="8" cy="22" r="1.3" fill="var(--sky)"/></svg></div>TOTAL SMS<br>MESSAGES</div>
<div class="abs stat-val" style="left:898px">0/0</div>

<h1 class="abs reports-h">REPORTS</h1>

<section class="abs panel"></section>
<div class="abs panel-rule"></div>
<div class="abs report-title">CLIENTS TOTAL : SERVED VS NON SERVED ( ACCOUNT )</div>
<div class="abs report-sub">From 23 December 2016 to 07 January 2017</div>
<div class="abs btn-green"></div>
<svg class="abs" style="left:739px;top:363px" width="15" height="16" viewBox="0 0 22 24"><circle cx="11" cy="7" r="6" fill="#fff"/><path d="M1 23 Q1 14 11 14 Q21 14 21 23Z" fill="#fff"/></svg>
<svg class="abs" style="left:798px;top:362px" width="18" height="18" viewBox="0 0 24 24"><g transform="rotate(-45 12 12)"><rect x="2" y="8" width="20" height="8" rx="1" fill="#555"/></g></svg>
<svg class="abs" style="left:857px;top:364px" width="18" height="15" viewBox="0 0 28 24"><ellipse cx="12" cy="9" rx="10" ry="7" fill="none" stroke="#555" stroke-width="2.5"/><path d="M16 18 Q22 19 25 15" fill="none" stroke="#555" stroke-width="2.5"/></svg>
<svg class="abs" style="left:920px;top:362px" width="10" height="17" viewBox="0 0 16 26"><rect x="1.5" y="1.5" width="13" height="23" rx="2" fill="none" stroke="#555" stroke-width="2.5"/></svg>
<div class="abs btn-orange"></div>
<svg class="abs" style="left:1000px;top:364px" width="34" height="16" viewBox="0 0 34 16"><path d="M1 1V15H20" stroke="#fff" stroke-width="1.6" fill="none"/><path d="M3 12 L8 7 L12 10 L19 3" stroke="#fff" stroke-width="1.8" fill="none"/><path d="M26 6 L29 9 L32 6" stroke="#fff" stroke-width="1.4" fill="none"/></svg>

<svg class="abs chart" width="935" height="430" viewBox="124 440 935 430" role="img" aria-label="Line chart of clients served per day">
  <g stroke="#e4e4e4" stroke-width="1">
    <line x1="201" y1="484" x2="982" y2="484"/><line x1="201" y1="538" x2="982" y2="538"/>
    <line x1="201" y1="592" x2="982" y2="592"/><line x1="201" y1="647" x2="982" y2="647"/>
    <line x1="201" y1="701" x2="982" y2="701"/><line x1="201" y1="756" x2="982" y2="756"/>
  </g>
  <g stroke="#333" stroke-width="1">
    <line x1="252" y1="756" x2="252" y2="766"/><line x1="316" y1="756" x2="316" y2="766"/><line x1="381" y1="756" x2="381" y2="766"/><line x1="446" y1="756" x2="446" y2="766"/><line x1="510" y1="756" x2="510" y2="766"/><line x1="575" y1="756" x2="575" y2="766"/><line x1="639" y1="756" x2="639" y2="766"/><line x1="704" y1="756" x2="704" y2="766"/><line x1="768" y1="756" x2="768" y2="766"/><line x1="834" y1="756" x2="834" y2="766"/><line x1="898" y1="756" x2="898" y2="766"/>
  </g>
  <g font-family="Montserrat,sans-serif" font-size="12" font-weight="600" text-anchor="middle" fill="#111">
    <text x="190" y="489">5</text><text x="190" y="543">4</text><text x="190" y="597">3</text><text x="190" y="652">2</text><text x="190" y="706">1</text><text x="190" y="761">0</text>
  </g>
  <g font-family="Montserrat,sans-serif" font-size="11" text-anchor="middle" fill="#444">
    <text x="251" y="793">DEC 24</text><text x="316" y="793">DEC 25</text><text x="379" y="793">DEC 26</text><text x="445" y="793">DEC 27</text><text x="510" y="793">DEC 28</text><text x="573" y="793">DEC 29</text><text x="640" y="793">DEC 30</text><text x="701" y="793">DEC 31</text><text x="764" y="793">JAN 1</text><text x="835" y="793">JAN 2</text><text x="896" y="793">JAN 3</text>
  </g>
  <text x="156" y="628" transform="rotate(-90 156 628)" text-anchor="middle" font-family="Montserrat,sans-serif" font-size="12" font-weight="600" fill="#111">CLIENTS</text>
  <polyline points="252,749 348,668 396,687 451,627 481,649 589,568 614,582 662,542 775,542 839,519 866,497 917,492" fill="none" stroke="var(--blue)" stroke-width="3" stroke-linejoin="round"/>
  <rect x="485" y="846" width="14" height="14" fill="var(--blue)"/>
  <text x="508" y="857" font-family="Montserrat,sans-serif" font-size="11.5" fill="#111">SERVED</text>
  <rect x="576" y="846" width="14" height="14" fill="#e6e6e6"/>
  <text x="597" y="857" font-family="Montserrat,sans-serif" font-size="11.5" fill="#111">NON SERVED</text>
</svg>

<section class="abs promo plans">
  <h2><svg width="22" height="20" viewBox="0 0 22 20"><rect x="1" y="4" width="15" height="15" rx="2" fill="none" stroke="#fff" stroke-width="2"/><path d="M8 12 L18 2 L21 5 L11 15 H8Z" fill="#fff"/></svg>PLANS</h2>
  <p>Neque porro quisquam est qui dolorem ipsum quia dolor sit amet, consectetur, adipisci velit...</p>
  <span class="cta">UPGRADE</span>
</section>
<section class="abs promo addons">
  <h2><svg width="22" height="20" viewBox="0 0 22 20"><path d="M1 6 H6 A3 3 0 1 1 11 6 H15 V10 A3 3 0 1 1 15 15 V19 H1Z" fill="#fff"/></svg>ADD-ONS</h2>
  <p>Neque porro quisquam est qui dolorem ipsum quia dolor sit amet, consectetur, adipisci velit...</p>
  <span class="cta">ACTIVATE</span>
</section>

<div class="abs footer-rule"></div>
<footer class="abs footer">© 2017 Company Name &nbsp;| All Rights Reserved</footer>
<div class="abs version">C5</div>

</body>
</html>
```